Business Cards for new orthopaedic surgery practice

My husband and I are starting our own orthopaedic surgery practice. We are looking for a business card that is uniform, but one will have my name/title and the other will have his. You can just create one design with my name on it for now. But when I choose your design as the winning design I will ask that you add another copy with his name/title.

We are looking for classy, simple, elite all in one. We like dark blues/a little gold/yellow. Something that goes with our logo. We want our logo incorporated. Here is all the info you need:
Business name: RV Bone & Vitality Center
Location: 38517 North Willowmere Ave
Palm Hollow, FL 33984
Phone: 954-218-4063
Fax: 954-582-7341
Email: info@myrvbonecare.example

Names: Lydia Vance, M.D.
Board Certified Hand and Upper Extremity Surgeon

Ebo Dansu, M.D.
Board Certified Hip & Knee Replacement/General Orthopaedic Surgeon

Can decide what you want to put on the back. Maybe a slogan:
Rooted in Care. Focused on You

I am just going to upload our logo. The only thing is if we select you as the winning design, the location, and phone numbers may change. We will need your help to update that once fully solidified.

Industry/Entity Type

Medical

Contact Information for Business Card

Colors
0054AA
0677BA
7BADD7
CADEEF
E8F1F8
0094D4
00A9DD
6FCCEA
C7EBF8
E9F6FB

Requirements
Must have
• class, appeal,
Should not have
• We want to air on the side of masculine if we are looking at masculine vs. feminine feel. But we still want it classy, sophisticated, and something we will love

```html
<!DOCTYPE html>
<html lang="en">
<head>
<meta charset="utf-8">
<title>RV Bone &amp; Vitality Center – Business Card</title>
<link href="https://fonts.googleapis.com/css2?family=Poppins:wght@400;500;600&display=swap" rel="stylesheet">
<style>
  :root {
    --backdrop: #1c1d21;
    --card-navy: #263d86;
    --card-navy-deep: #1f3374;
    --accent-cyan: #1cb4e3;
    --ink-white: #ffffff;
    --soft-periwinkle: #5d76c8;
  }
  * { box-sizing: border-box; margin: 0; padding: 0; }
  html, body {
    width: 1200px; height: 900px; overflow: hidden;
    background: var(--backdrop);
    font-family: "Poppins", sans-serif;
    color: var(--ink-white);
  }
  .sheet {
    width: 1200px; height: 900px;
    display: flex; flex-direction: column;
    align-items: center; justify-content: center; gap: 40px;
  }
  .card {
    position: relative;
    width: 700px; height: 400px;
    background: var(--card-navy);
    box-shadow: 0 10px 30px rgba(0,0,0,.45);
    overflow: hidden;
  }

  /* ---------- front ---------- */
  .brand {
    position: absolute; top: 48px; left: 0; right: 0;
    display: flex; justify-content: center; align-items: center; gap: 18px;
  }
  .brand-mark {
    width: 62px; height: 62px; border: 3px solid var(--ink-white);
  }
  .brand-divider {
    width: 2px; height: 92px; background: var(--ink-white);
  }
  .brand-name {
    font-weight: 600; font-size: 23px; line-height: 1.12;
    letter-spacing: 1.5px; text-transform: uppercase;
    color: var(--ink-white);
  }
  .identity {
    position: absolute; top: 196px; left: 0; right: 0;
    display: flex; align-items: center; gap: 14px; padding: 0 40px;
  }
  .identity-rule { flex: 1; height: 1px; background: var(--ink-white); }
  .identity-text { text-align: center; }
  .person-name {
    font-weight: 600; font-size: 22px; color: var(--accent-cyan); letter-spacing: .5px;
  }
  .person-title {
    font-size: 14px; color: var(--ink-white); margin-top: 2px;
  }
  .contact-list {
    position: absolute; left: 48px; bottom: 44px;
    list-style: none; font-size: 14px; line-height: 1.75;
  }
  .contact-list li { display: flex; align-items: center; gap: 9px; }
  .contact-icon { width: 14px; height: 14px; fill: var(--accent-cyan); flex: none; }
  .address {
    position: absolute; right: 48px; bottom: 48px;
    font-size: 14px; line-height: 1.6; text-align: left; font-style: normal;
  }

  /* ---------- back ---------- */
  .back-decoration {
    position: absolute; left: 0; top: 0; width: 430px; height: 400px;
    background: linear-gradient(135deg, var(--card-navy-deep) 0%, var(--card-navy) 45%, var(--soft-periwinkle) 100%);
    opacity: .55;
  }
  .back-block {
    position: absolute; right: 60px; bottom: 58px;
    display: flex; gap: 22px; align-items: stretch;
  }
  .back-divider { width: 2px; background: var(--ink-white); transform: skewX(-14deg); }
  .back-name {
    font-weight: 600; font-size: 28px; line-height: 1.12;
    letter-spacing: 1.5px; text-transform: uppercase; color: var(--ink-white);
  }
  .slogan {
    margin-top: 18px; font-size: 16px; line-height: 1.45; color: var(--ink-white);
  }
</style>
</head>
<body>
<main class="sheet">

  <section class="card card-front" aria-label="Business card front">
    <div class="brand">
      <div class="brand-mark" aria-hidden="true"></div>
      <div class="brand-divider" aria-hidden="true"></div>
      <div class="brand-name">RV Bone &amp;<br>Vitality<br>Center</div>
    </div>

    <div class="identity">
      <span class="identity-rule"></span>
      <div class="identity-text">
        <div class="person-name">Lydia Vance, M.D.</div>
        <div class="person-title">Hand and Upper Extremity Surgery</div>
      </div>
      <span class="identity-rule"></span>
    </div>

    <ul class="contact-list">
      <li>
        <svg class="contact-icon" viewBox="0 0 24 24" aria-label="Phone"><path d="M6.6 10.8a15.1 15.1 0 0 0 6.6 6.6l2.2-2.2a1 1 0 0 1 1-.25 11.4 11.4 0 0 0 3.6.57 1 1 0 0 1 1 1V20a1 1 0 0 1-1 1A17 17 0 0 1 3 4a1 1 0 0 1 1-1h3.5a1 1 0 0 1 1 1c0 1.25.2 2.45.57 3.6a1 1 0 0 1-.25 1z"/></svg>
        954-218-4063
      </li>
      <li>
        <svg class="contact-icon" viewBox="0 0 24 24" aria-label="Fax"><path d="M6 2h9l3 3v4H6zM4 10h16a2 2 0 0 1 2 2v7h-4v3H6v-3H2v-7a2 2 0 0 1 2-2zm4 7v3h8v-3z"/></svg>
        954-582-7341
      </li>
      <li>
        <svg class="contact-icon" viewBox="0 0 24 24" aria-label="Email"><path d="M2 5h20v14H2zm2 2v.5l8 5 8-5V7zm0 2.9V17h16V9.9l-8 5z"/></svg>
        info@myrvbonecare.example
      </li>
    </ul>

    <address class="address">
      38517 North Willowmere Ave<br>
      Palm Hollow, FL 33984
    </address>
  </section>

  <section class="card card-back" aria-label="Business card back">
    <div class="back-decoration" role="img" aria-label="Large faint brand monogram decoration"></div>
    <div class="back-block">
      <div class="back-divider" aria-hidden="true"></div>
      <div>
        <div class="back-name">RV Bone &amp;<br>Vitality<br>Center</div>
        <p class="slogan">Steady in Care<br>Centered on You</p>
      </div>
    </div>
  </section>

</main>
</body>
</html>
```